Summit Bodyform Gym Website

We need a website design for our gym.

Summit is the UAE's first calisthenics and parkour gym. The theme under which the gym revolves is that one does not require any machinery to workout as our bodies could be themselves the machinery. The gym is designed to be the more of a social hub rather than an "in-and-out" gym, where people come train, have fun, hang out and socialize for a few hours rather than just train for 60 minutes then leave. The gym is designed to be a big open space with lots of natural sunlight, natural wood and plants all over the place to create a natural and refreshing setting. We also use recycled material throughout the gym and recycle our waste as being green is part of our philosophy. We currently also have some of the world's top and most recognized calisthenics athletes working with us.

We would like our website to reflect all that as well as provide a simple, interactive and fun way for visitors to be able to get class and gym information, check out gym media and contact us for bookings.

Target Market(s)

Ages 15-35

Industry/Entity Type

Fitness

Coding

Coded - Design and coding required

Number of Pages Required

4 page

Font styles to use
Decorative

Colors
0792cd

Requirements
Must have
• Class descriptions
• Gym description
• Class schedules
• Trainer profiles
• Gym philosophy
• Contact Details
Nice to have
• A link to contact us directly for a free first trial class

```html
<!DOCTYPE html>
<html lang="en">
<head>
<meta charset="utf-8">
<title>Summit Bodyform Gym</title>
<link rel="stylesheet" href="https://fonts.googleapis.com/css2?family=Roboto:wght@400;500;700&family=Roboto+Condensed:wght@400;700&display=swap">
<style>
:root{
  --brand:#0792cd;
  --ink:#1c1c1c;
  --nav:#2b2b2b;
  --panel:#ececec;
  --footer-left:#3b3b3b;
  --footer-right:#333333;
  --footer-bar:#1f1f1f;
  --white:#ffffff;
}
*{box-sizing:border-box;margin:0;padding:0}
html,body{width:1200px;height:2970px;overflow:hidden}
body{font-family:"Roboto",Arial,sans-serif;color:var(--ink);background:var(--white);position:relative}
.btn{display:inline-block;background:var(--brand);color:var(--white);font-family:"Roboto Condensed",Arial,sans-serif;font-size:15px;padding:14px 22px;text-decoration:none}
.accent{color:var(--brand)}
.dots{display:flex;gap:12px;justify-content:center}
.dots span{width:10px;height:10px;border-radius:50%;background:var(--white)}
.dots span.on{background:var(--brand)}

/* hero */
.hero{position:absolute;left:0;top:0;width:1200px;height:582px;background:linear-gradient(180deg,#4a3526 0%,#5e4330 45%,#3a2c22 75%,#2a2522 100%);text-align:center;color:var(--white)}
.hero-photo{position:absolute;inset:0}
.brand-name{position:absolute;top:76px;left:0;width:100%;font-size:46px;font-weight:700;letter-spacing:-.5px}
.hero h1{position:absolute;top:316px;width:100%;font-size:34px;font-weight:500}
.hero .lead{position:absolute;top:366px;width:100%;font-family:"Roboto Condensed",Arial,sans-serif;font-size:17px}
.hero .btn{position:absolute;top:412px;left:532px;width:136px;padding:16px 0;font-size:14px}
.hero .dots{position:absolute;top:547px;width:100%}

/* nav */
.main-nav{position:absolute;top:582px;left:0;width:1200px;height:54px;background:var(--nav);display:flex;padding-left:78px;font-family:"Roboto Condensed",Arial,sans-serif;font-size:14px}
.main-nav a{color:var(--brand);text-decoration:none;line-height:54px;margin-right:68px;position:relative}
.main-nav a.active{background:var(--brand);color:var(--white);padding:0 26px;margin-right:50px}
.main-nav a.active:after{content:"";position:absolute;left:50%;bottom:-8px;margin-left:-8px;border:8px solid transparent;border-bottom:0;border-top-color:var(--brand)}

/* welcome */
.welcome{position:absolute;top:636px;left:0;width:1200px;height:298px;text-align:center}
.welcome h2{margin-top:42px;font-size:38px;font-weight:700}
.welcome p{width:830px;margin:10px auto 0;font-family:"Roboto Condensed",Arial,sans-serif;font-size:11.5px;line-height:19px;color:#333}
.welcome .btn{margin-top:16px;padding:12px 14px;font-size:14px}

/* gym description */
.gym-desc{position:absolute;top:934px;left:0;width:1200px;height:542px;background:linear-gradient(90deg,#2a2a2a,#1f1f1f 60%,#2c2a28);color:var(--white)}
.gym-desc .frame{position:absolute;left:44px;top:38px;width:384px;height:470px;border:8px solid var(--white);background:linear-gradient(180deg,#6b6b6b,#3b3b3b 60%,#9a9a9a)}
.gym-desc .copy{position:absolute;left:478px;top:66px;width:600px;text-align:center}
.gym-desc h2{font-size:36px;font-weight:700}
.gym-desc h3{margin-top:14px;font-size:25px;font-weight:500;letter-spacing:.5px}
.gym-desc p{margin-top:24px;font-family:"Roboto Condensed",Arial,sans-serif;font-size:11.5px;line-height:23px}
.gym-desc .btn{margin-top:26px;padding:12px 14px;font-size:14px}

/* schedules */
.schedules{position:absolute;top:1476px;left:0;width:1200px;height:600px}
.schedules h2{text-align:center;margin-top:46px;font-size:36px;font-weight:700}
.day-tabs{position:absolute;top:134px;left:142px;display:flex;font-family:"Roboto Condensed",Arial,sans-serif;font-size:16px}
.day-tabs li{list-style:none;width:131px;height:60px;line-height:60px;text-align:center;border-right:1px solid #e0e0e0;color:#222}
.day-tabs li:last-child{border-right:0}
.day-tabs li.on{background:var(--panel)}
.slots{position:absolute;top:194px;left:0;width:1200px;height:406px;background:var(--panel);padding-top:26px;font-family:"Roboto Condensed",Arial,sans-serif}
.slot{display:flex;align-items:center;height:94px;position:relative}
.slot .time{position:absolute;left:190px;width:100px;text-align:center;font-size:16px;line-height:22px}
.slot .time b{display:block;color:var(--brand);font-weight:400}
.slot .trainer{position:absolute;width:200px;text-align:center;font-size:15px;line-height:30px}
.slot .trainer b{display:block;color:var(--brand);font-weight:700}
.slot .t1{left:386px}.slot .t2{left:634px}
.slot .btn{position:absolute;left:940px;padding:12px 8px;font-size:13px}

/* trainers */
.trainers{position:absolute;top:2076px;left:0;width:1200px;height:544px;background:linear-gradient(90deg,#1d1d1d,#3d3d3d 40%,#2b2b2b 70%,#4a4a4a)}
.trainers h2{text-align:center;margin-top:42px;font-size:36px;font-weight:700;color:var(--white)}
.cards{position:absolute;top:128px;left:124px;display:flex;gap:58px}
.card{width:278px}
.card .photo{height:258px;background:linear-gradient(160deg,#8a8a8a,#2e2e2e)}
.card .info{height:96px;background:var(--white);text-align:center;padding-top:16px}
.card h4{color:var(--brand);font-size:17px;font-weight:500}
.card p{margin-top:8px;font-family:"Roboto Condensed",Arial,sans-serif;font-size:11.5px;line-height:22px;color:#333}
.trainers .dots{position:absolute;top:507px;width:100%}

/* footer */
.site-footer{position:absolute;top:2620px;left:0;width:1200px;height:296px;display:flex;color:var(--white)}
.site-footer section{text-align:center}
.hours{width:600px;background:var(--footer-left)}
.connect{width:600px;background:var(--footer-right)}
.site-footer h5{margin-top:82px;font-size:17px;font-weight:400}
.hour-list{display:flex;justify-content:center;gap:34px;margin-top:40px;text-align:left}
.hour{display:flex;gap:14px;align-items:center}
.hour .icon{width:60px;height:64px;background:#282828;display:flex;align-items:center;justify-content:center}
.hour b{display:block;font-size:16px;font-weight:500}
.hour span{font-size:12px}
.social{display:flex;justify-content:center;gap:32px;margin-top:40px}
.social a{width:60px;height:64px;background:#444;display:flex;align-items:center;justify-content:center}
.social a i{width:14px;height:14px;border-radius:50%;background:var(--white)}
.footer-bar{position:absolute;top:2916px;left:0;width:1200px;height:54px;background:var(--footer-bar);color:#ddd;font-size:10px;display:flex;justify-content:space-between;align-items:center;padding:0 104px}
.footer-bar nav a{color:#ddd;text-decoration:none}
</style>
</head>
<body>

<header class="hero">
  <div class="hero-photo" role="img" aria-label="Gym wall with living plant letters above a rack of dumbbells"></div>
  <div class="brand-name">Summit Bodyform Gym</div>
  <h1>Gym in UAE</h1>
  <p class="lead">Summit is the UAE's first calisthenics and parkour gym</p>
  <a class="btn" href="#">Free First Trial Class</a>
  <div class="dots"><span></span><span class="on"></span><span></span></div>
</header>

<nav class="main-nav">
  <a class="active" href="#">Home</a>
  <a href="#">Class descriptions</a>
  <a href="#">Gym description</a>
  <a href="#">Class schedules</a>
  <a href="#">Trainer profiles</a>
  <a href="#">Gym philosophy</a>
  <a href="#">Contact</a>
</nav>

<section class="welcome">
  <h2>Welcome to <span class="accent">&nbsp;Summit</span></h2>
  <p>Lorem Ipsum is simply dummy text of the printing and typesetting industry. Lorem Ipsum has been the industry's standard dummy text ever since the 1500s, when an unknown printer took a galley of type and scrambled it to make a type specimen book. It has survived not only five centuries, but also the leap into electronic typesetting, remaining essentially unchanged. It was popularised in the 1960s with the release of Letraset sheets containing Lorem Ipsum passages, and more recently with desktop publishing software like Aldus PageMaker including versions of Lorem Ipsum.</p>
  <a class="btn" href="#">View Info</a>
</section>

<section class="gym-desc">
  <div class="frame" role="img" aria-label="Athlete training on gymnastic rings"></div>
  <div class="copy">
    <h2>Gym <span class="accent">Description</span></h2>
    <h3>WORKOUT AND FITNESS IS A LIFE STYLE</h3>
    <p>Lorem Ipsum is simply dummy text of the printing and typesetting industry. Lorem Ipsum has been the industry's standard dummy text ever since the 1500s, when an unknown printer took a galley of type and scrambled it to make a type specimen book. It has survived not only five centuries, but also the leap into electronic typesetting, remaining essentially unchanged. It was popularised in the 1960s with the release of Letraset sheets containing Lorem Ipsum passages, and more recently with desktop publishing software like Aldus PageMaker including versions of Lorem Ipsum.</p>
    <p>but also the leap into electronic typesetting, remaining essentially unchanged. It was popularised in the 1960s with the release of Letraset sheets containing Lorem Ipsum passages, and more recently with desktop publishing software like Aldus PageMaker including versions of Lorem Ipsum.</p>
    <a class="btn" href="#">View Info</a>
  </div>
</section>

<section class="schedules">
  <h2>Class <span class="accent">Schedules</span></h2>
  <ul class="day-tabs">
    <li class="on">Monday</li><li>Tuesday</li><li>Wednesday</li><li>Thursday</li><li>Friday</li><li>Saturday</li><li>Sunday</li>
  </ul>
  <div class="slots">
    <div class="slot"><div class="time"><b>13:00</b>1 hour</div><div class="trainer t1"><b>Marek Oshiro</b>Experienced</div><div class="trainer t2"><b>Oshiro Marek</b>10 year Experienced</div><a class="btn" href="#">Book Class</a></div>
    <div class="slot"><div class="time"><b>13:00</b>1 hour</div><div class="trainer t1"><b>Marek Oshiro</b>Experienced</div><div class="trainer t2"><b>Oshiro Marek</b>10 year Experienced</div><a class="btn" href="#">Book Class</a></div>
    <div class="slot"><div class="time"><b>13:00</b>1 hour</div><div class="trainer t1"><b>Marek Oshiro</b>Experienced</div><div class="trainer t2"><b>Oshiro Marek</b>10 year Experienced</div><a class="btn" href="#">Book Class</a></div>
    <div class="slot"><div class="time"><b>13:00</b>1 hour</div><div class="trainer t1"><b>Marek Oshiro</b>Experienced</div><div class="trainer t2"><b>Oshiro Marek</b>10 year Experienced</div><a class="btn" href="#">Book Class</a></div>
  </div>
</section>

<section class="trainers" role="img" aria-label="Dim gym backdrop with athlete silhouettes">
  <h2>Trainer <span class="accent">Profile</span></h2>
  <div class="cards">
    <article class="card"><div class="photo" role="img" aria-label="Trainer portrait on a staircase"></div><div class="info"><h4>NADIA CORWELL</h4><p>Lorem Ipsum is simply dummy text of the printing<br>and typesetting industry.</p></div></article>
    <article class="card"><div class="photo" role="img" aria-label="Trainer hanging upside down from a bar"></div><div class="info"><h4>OSHIRO</h4><p>Lorem Ipsum is simply dummy text of the printing<br>and typesetting industry.</p></div></article>
    <article class="card"><div class="photo" role="img" aria-label="Trainer holding a planche under a skylight"></div><div class="info"><h4>MAREK</h4><p>Lorem Ipsum is simply dummy text of the printing<br>and typesetting industry.</p></div></article>
  </div>
  <div class="dots"><span></span><span class="on"></span><span></span></div>
</section>

<footer class="site-footer">
  <section class="hours">
    <h5>Opening hours</h5>
    <div class="hour-list">
      <div class="hour"><span class="icon"><svg width="38" height="38" viewBox="0 0 38 38"><circle cx="19" cy="19" r="16" fill="none" stroke="#0792cd" stroke-width="2.5"/><path d="M19 9v10l7 4" fill="none" stroke="#0792cd" stroke-width="2.5" stroke-linecap="round"/></svg></span><div><b>Mon - Fri</b><span>8:00 am - 10:00 pm</span></div></div>
      <div class="hour"><span class="icon"><svg width="38" height="38" viewBox="0 0 38 38"><circle cx="19" cy="19" r="16" fill="none" stroke="#0792cd" stroke-width="2.5"/><path d="M19 9v10l7 4" fill="none" stroke="#0792cd" stroke-width="2.5" stroke-linecap="round"/></svg></span><div><b>Sat - Sun</b><span>8:00 am - 10:00 pm</span></div></div>
    </div>
  </section>
  <section class="connect">
    <h5>Connect with us</h5>
    <div class="social">
      <a href="#" aria-label="Social link 1"><i></i></a>
      <a href="#" aria-label="Social link 2"><i></i></a>
      <a href="#" aria-label="Social link 3"><i></i></a>
      <a href="#" aria-label="Social link 4"><i></i></a>
    </div>
  </section>
</footer>

<div class="footer-bar">
  <span>Copyright © 2015 Summit Bodyform Gym. All Rights Reserved.</span>
  <nav><a href="#">Terms &amp; Conditions</a> &nbsp;/&nbsp; <a href="#">Privacy &amp; Disclaimer</a> &nbsp;/&nbsp; <a href="#">Returns &amp; Refunds</a></nav>
</div>

</body>
</html>
```